Road Construction Company needs business cards

We would like a new business card designed for our business.

We're a road construction company based in Qld, Australia.

Can the business card please have the following information on it.

Name: Warren Halbeck
Position: General Manager
Phone: 0472 915 348
Email: Warren.halbeck@tovrin.com.au
Address: 87 Marrow Ave, Pendlebay, QLD, 4023
Website: www.tovrin.com.au

Visually we'd like the card to be professional and simple.

Attached is our logo.

Our website is www.tovrin.com.au

Target Market(s)

Men aged 25-60

Contact Information for Business Card

As listed in project description

Font styles to use
Serif

Requirements
Must have
• Large logo on back of card

```html
<!DOCTYPE html>
<html lang="en">
<head>
<meta charset="utf-8">
<title>Tovrin Business Card</title>
<link rel="stylesheet" href="https://fonts.googleapis.com/css2?family=Open+Sans:wght@400;600;700;800&display=swap">
<style>
  :root {
    --backdrop: #1b1b1b;
    --paper: #ffffff;
    --brand-blue: #1456a8;
    --accent-blue: #2f8fd6;
    --ink: #1e1e1e;
    --map-grey: #e4e5e7;
  }
  * { box-sizing: border-box; margin: 0; padding: 0; }
  html, body { width: 1200px; height: 780px; overflow: hidden; }
  body {
    background: var(--backdrop);
    font-family: "Open Sans", Arial, sans-serif;
    display: flex;
    align-items: center;
    justify-content: center;
    gap: 40px;
  }
  .card {
    position: relative;
    width: 540px;
    height: 309px;
    background: var(--paper);
    overflow: hidden;
  }
  .wordmark {
    font-weight: 800;
    color: var(--brand-blue);
    letter-spacing: 0.04em;
    text-transform: uppercase;
    line-height: 1;
  }

  /* Back side */
  .card-back .world-map {
    position: absolute;
    left: 40px; top: 30px;
    width: 460px; height: 240px;
    background: radial-gradient(ellipse at center, var(--map-grey) 0%, #eff0f1 60%, var(--paper) 100%);
    border-radius: 40%;
  }
  .card-back .wordmark {
    position: absolute;
    left: 0; right: 0; top: 118px;
    text-align: center;
    font-size: 70px;
  }

  /* Front side */
  .card-front .wordmark {
    position: absolute;
    left: 150px; top: 56px;
    font-size: 56px;
  }
  .person {
    position: absolute;
    left: 48px; top: 176px;
    width: 210px;
    text-align: right;
  }
  .person-name {
    font-size: 25px;
    font-weight: 700;
    color: var(--brand-blue);
    line-height: 1.1;
  }
  .person-role {
    font-size: 15px;
    color: var(--ink);
    margin-top: 2px;
  }
  .divider {
    position: absolute;
    left: 276px; top: 160px;
    width: 1px; height: 82px;
    background: var(--ink);
  }
  .contact-list {
    position: absolute;
    left: 292px; top: 164px;
    list-style: none;
  }
  .contact-list li {
    display: flex;
    align-items: center;
    gap: 8px;
    font-size: 13.5px;
    color: var(--ink);
    line-height: 25px;
  }
  .contact-list svg { width: 13px; height: 13px; flex: none; }
  .address-band {
    position: absolute;
    left: 0; right: 0; top: 256px;
    height: 30px;
    background: var(--brand-blue);
    color: var(--paper);
    font-size: 14px;
    line-height: 30px;
    text-align: center;
  }
</style>
</head>
<body>
  <section class="card card-back">
    <div class="world-map" role="img" aria-label="Faint dotted world map in light grey"></div>
    <div class="wordmark">Tovrin</div>
  </section>

  <section class="card card-front">
    <div class="wordmark">Tovrin</div>

    <div class="person">
      <p class="person-name">Warren Halbeck</p>
      <p class="person-role">General Manager</p>
    </div>

    <div class="divider"></div>

    <ul class="contact-list">
      <li>
        <svg viewBox="0 0 14 14" aria-hidden="true"><path fill="var(--accent-blue)" d="M3 1l2.5 3-1.3 1.5c.8 1.7 2.1 3 3.8 3.8L9.5 8 12.5 10.5 11 13C5.5 12.5 1.5 8.5 1 3z"/></svg>
        0472 915 348
      </li>
      <li>
        <svg viewBox="0 0 14 14" aria-hidden="true"><circle cx="7" cy="7" r="6" fill="none" stroke="var(--accent-blue)" stroke-width="1.5"/><path d="M1 7h12M7 1c-3 3-3 9 0 12M7 1c3 3 3 9 0 12" fill="none" stroke="var(--accent-blue)" stroke-width="1.2"/></svg>
        www.tovrin.com.au
      </li>
      <li>
        <svg viewBox="0 0 14 14" aria-hidden="true"><rect x="1" y="3" width="12" height="8" fill="var(--accent-blue)"/><path d="M1 3l6 5 6-5" fill="none" stroke="#fff" stroke-width="1.2"/></svg>
        Warren.halbeck@tovrin.com.au
      </li>
    </ul>

    <div class="address-band">87 Marrow Ave, Pendlebay, QLD, 4023</div>
  </section>
</body>
</html>
```